Design a Website for an IT Support Company

We are an IT support company that provides commercial IT support and services to small and medium sized businesses. We are in need of a website to be developed for our business.
We would like to work with someone who is either familiar with the IT field, or has developed a website for an IT support company in the past.
Some examples of designs/layouts that we like:
https://www.veldaworks.example/
http://www.marsbyquill.example/
http://817kq.example/
http://www.olbenstructures.example/
http://www.bykq.example/
I have attached a word document that gives a menu system/page layout format that we would like for our website as well as branch office phone numbers. Our logo is also attached that you can use for your design purposes. We currently do not have copy produced for all of the pages outlined in the word document, but would get this done during the project with the selected designer.
We would like the website to be SEO friendly & fully responsive. We would prefer a Wordpress format, however, we are open to HTML formats as well.

```html
<!DOCTYPE html>
<html lang="en">
<head>
<meta charset="utf-8">
<title>Vantora IT — IT Support for Growing Businesses</title>
<link rel="stylesheet" href="https://fonts.googleapis.com/css2?family=Roboto:wght@400;500;700&family=Poppins:wght@400;500;600&display=swap">
<style>
  :root {
    --brand-blue: #1a6fb5;
    --button-blue: #1672bd;
    --ink: #1f1f1f;
    --body-text: #4a4a4a;
    --muted: #8a8a8a;
    --band: #f3f3f1;
    --white: #ffffff;
    --footer-bg: #141414;
    --footer-text: #c9c9c9;
    --footer-line: #3a3a3a;
    --icon-ring: #6c6c6c;
  }
  * { box-sizing: border-box; margin: 0; padding: 0; }
  html, body { width: 1200px; height: 2350px; overflow: hidden; }
  body {
    position: relative;
    background: var(--white);
    font-family: "Poppins", sans-serif;
    color: var(--ink);
  }
  .abs { position: absolute; }

  /* Header */
  .site-header { left: 0; top: 0; width: 1200px; height: 67px; background: var(--white); }
  .brand { left: 97px; top: 14px; display: flex; align-items: center; gap: 10px; }
  .brand-mark { width: 26px; height: 26px; border-radius: 50%; background: var(--brand-blue); }
  .brand-name { font-family: "Roboto", sans-serif; font-weight: 500; font-size: 26px; color: var(--ink); }
  .main-nav { left: 0; top: 25px; width: 1200px; }
  .main-nav a {
    position: absolute; font-family: "Roboto", sans-serif; font-size: 14px;
    color: var(--ink); text-decoration: none; letter-spacing: .3px; white-space: nowrap;
  }

  /* Hero */
  .hero { left: 0; top: 67px; width: 1200px; height: 494px; }
  .hero-photo {
    position: absolute; inset: 0;
    background: linear-gradient(100deg, #6b5a46 0%, #a8895c 25%, #c6b08a 48%, #9fa3a8 70%, #d6d8da 100%);
  }
  .hero-shade { position: absolute; inset: 0; background: rgba(40,30,20,.18); }
  .hero-title {
    left: 0; top: 175px; width: 1200px; text-align: center;
    font-family: "Roboto", sans-serif; font-weight: 700; font-size: 38px; color: var(--white); letter-spacing: .5px;
  }
  .hero-sub {
    left: 0; top: 240px; width: 1200px; text-align: center;
    font-family: "Roboto", sans-serif; font-weight: 500; font-size: 31px; color: var(--white); letter-spacing: .5px;
  }
  .btn {
    display: flex; align-items: center; justify-content: center;
    background: var(--button-blue); color: var(--white);
    font-family: "Roboto", sans-serif; font-weight: 500; text-decoration: none; border-radius: 2px;
  }
  .hero-cta { left: 490px; top: 311px; width: 220px; height: 54px; font-size: 18px; }

  /* Services */
  .services { left: 0; top: 561px; width: 1200px; height: 287px; background: var(--band); }
  .service { top: 72px; width: 370px; height: 160px; }
  .service-icon {
    position: absolute; left: 0; top: 0; width: 80px; height: 80px; border-radius: 50%;
    border: 2px solid var(--icon-ring); background: var(--white);
    display: flex; align-items: center; justify-content: center;
  }
  .service-title { position: absolute; left: 102px; top: 4px; font-family: "Roboto", sans-serif; font-weight: 500; font-size: 19px; }
  .service-text { position: absolute; left: 102px; top: 40px; width: 230px; font-size: 11px; line-height: 20px; color: var(--body-text); }
  .read-link {
    position: absolute; left: 102px; top: 129px; font-size: 11px; font-weight: 500; color: var(--ink);
    letter-spacing: .5px; display: flex; align-items: center; gap: 8px;
  }

  /* Why */
  .why { left: 0; top: 848px; width: 1200px; height: 291px; background: var(--white); }
  .section-title {
    position: absolute; left: 0; width: 1200px; text-align: center;
    font-family: "Roboto", sans-serif; font-weight: 700; font-size: 31px; color: var(--brand-blue);
  }
  .why-lead {
    position: absolute; left: 0; top: 116px; width: 1200px; text-align: center;
    font-family: "Roboto", sans-serif; font-size: 19px; color: var(--ink);
  }
  .why-body {
    position: absolute; left: 200px; top: 160px; width: 800px; text-align: center;
    font-size: 11px; line-height: 27px; color: var(--body-text);
  }

  /* Blog */
  .blog { left: 0; top: 1139px; width: 1200px; height: 744px; background: var(--band); }
  .blog-intro {
    position: absolute; left: 170px; top: 110px; width: 860px; text-align: center;
    font-size: 11px; line-height: 25px; color: var(--muted);
  }
  .post { top: 190px; width: 484px; }
  .post-image { width: 484px; height: 301px; border-radius: 4px; }
  .post-image.office { background: linear-gradient(160deg, #2c4a6e 0%, #dfe2e4 30%, #e9e9e6 60%, #8a6d4e 100%); }
  .post-image.tablet { background: linear-gradient(120deg, #3d5a80 0%, #b9c6d3 40%, #e8eaec 65%, #cfd94a 100%); }
  .post-title { margin-top: 22px; font-family: "Roboto", sans-serif; font-weight: 500; font-size: 17px; color: var(--ink); }
  .post-text { margin-top: 22px; font-size: 11px; line-height: 23px; color: var(--body-text); }
  .post-btn { margin-top: 23px; width: 119px; height: 37px; font-size: 14px; border-radius: 4px; }

  .divider { left: 97px; top: 1883px; width: 1009px; height: 1px; background: #dcdcdc; }

  /* Subscribe */
  .subscribe { left: 406px; top: 1935px; display: flex; }
  .subscribe-input {
    width: 296px; height: 38px; border: 1px solid #9a9a9a; background: var(--white);
    padding-left: 18px; display: flex; align-items: center; font-size: 11px; color: #666; letter-spacing: .4px;
  }
  .subscribe-btn {
    width: 100px; height: 38px; background: #262626; color: var(--white);
    font-size: 9px; font-weight: 600; letter-spacing: .8px; display: flex; align-items: center; justify-content: center;
  }

  /* Footer */
  .site-footer { left: 0; top: 2017px; width: 1200px; height: 333px; background: var(--footer-bg); color: var(--footer-text); }
  .footer-col { position: absolute; top: 26px; }
  .footer-col h4 { font-family: "Roboto", sans-serif; font-weight: 500; font-size: 14px; color: #dcdcdc; margin-bottom: 16px; }
  .footer-col.account h4 { margin-bottom: 8px; }
  .footer-col a { display: block; font-size: 12px; line-height: 21.5px; color: var(--footer-text); text-decoration: none; }
  .footer-col p { width: 300px; font-size: 10px; line-height: 22px; color: var(--footer-text); text-align: justify; }
  .footer-rule { left: 97px; top: 189px; width: 1009px; height: 1px; background: var(--footer-line); }
  .social { left: 102px; top: 225px; display: flex; gap: 12px; }
  .social span { width: 32px; height: 32px; border-radius: 50%; border: 1px solid #8a8a8a; }
  .copyright { left: 102px; top: 276px; font-size: 12px; color: var(--footer-text); }
  .footer-brand { left: 0; top: 222px; width: 1200px; display: flex; justify-content: center; align-items: center; gap: 10px; }
  .footer-brand .brand-mark { width: 26px; height: 26px; }
  .footer-brand .brand-name { color: var(--white); }
  .footer-links { left: 0; top: 286px; width: 1200px; display: flex; justify-content: center; gap: 14px; }
  .footer-links a { font-size: 12px; color: var(--footer-text); text-decoration: none; }
  .footer-phone { right: 95px; top: 232px; font-family: "Roboto", sans-serif; font-size: 26px; color: #bdbdbd; letter-spacing: 1.5px; }
  .footer-email { right: 95px; top: 276px; font-size: 12px; color: var(--footer-text); }
</style>
</head>
<body>

<header class="site-header abs">
  <div class="brand abs"><span class="brand-mark"></span><span class="brand-name">Vantora IT</span></div>
  <nav class="main-nav abs">
    <a href="#" style="left:470px">HOME</a>
    <a href="#" style="left:572px">ABOUT US</a>
    <a href="#" style="left:703px">SERVICES</a>
    <a href="#" style="left:834px">WHY VANTORA IT</a>
    <a href="#" style="left:1014px">CONTACT US</a>
  </nav>
</header>

<section class="hero abs">
  <div class="hero-photo" role="img" aria-label="Warm-toned office scene of staff working at computer monitors"></div>
  <div class="hero-shade"></div>
  <h1 class="hero-title abs">COMMITTED TO PEOPLE</h1>
  <p class="hero-sub abs">For The Next Generation Of Big Businesses</p>
  <a class="btn hero-cta abs" href="#">GET STARTED</a>
</section>

<section class="services abs">
  <article class="service abs" style="left:53px">
    <div class="service-icon">
      <svg width="32" height="36" viewBox="0 0 32 36"><g fill="var(--brand-blue)"><ellipse cx="16" cy="6" rx="14" ry="5"/><path d="M2 10c0 3 6 5 14 5s14-2 14-5v6c0 3-6 5-14 5S2 19 2 16z"/><path d="M2 20c0 3 6 5 14 5s14-2 14-5v8c0 3-6 5-14 5S2 31 2 28z"/></g></svg>
    </div>
    <h3 class="service-title">Data</h3>
    <p class="service-text">Lorem Ipsum is simply dummy text of the printing and typesetting industry. Lorem Ipsum has been the industry's 1500s been the industry's 1500s</p>
    <span class="read-link">READ MORE <svg width="10" height="10" viewBox="0 0 10 10"><circle cx="5" cy="5" r="5" fill="var(--ink)"/><path d="M4 3l2 2-2 2" stroke="#fff" stroke-width="1.3" fill="none"/></svg></span>
  </article>
  <article class="service abs" style="left:431px">
    <div class="service-icon">
      <svg width="46" height="32" viewBox="0 0 46 32"><path fill="var(--brand-blue)" d="M10 28a9 9 0 0 1-1-18 12 12 0 0 1 23-2 9 9 0 0 1 6 16H10z"/><circle cx="35" cy="24" r="7" fill="var(--brand-blue)" stroke="#fff" stroke-width="2"/><circle cx="35" cy="24" r="2.5" fill="#fff"/></svg>
    </div>
    <h3 class="service-title">Cloud</h3>
    <p class="service-text">Lorem Ipsum is simply dummy text of the printing and typesetting industry. Lorem Ipsum has been the industry's 1500s been the industry's 1500s</p>
    <span class="read-link">READ MORE <svg width="10" height="10" viewBox="0 0 10 10"><circle cx="5" cy="5" r="5" fill="var(--ink)"/><path d="M4 3l2 2-2 2" stroke="#fff" stroke-width="1.3" fill="none"/></svg></span>
  </article>
  <article class="service abs" style="left:816px">
    <div class="service-icon">
      <svg width="24" height="42" viewBox="0 0 24 42"><rect x="1.5" y="1.5" width="21" height="39" rx="3" fill="none" stroke="var(--brand-blue)" stroke-width="3"/><rect x="5" y="7" width="14" height="25" fill="var(--brand-blue)"/><circle cx="12" cy="36" r="1.8" fill="var(--brand-blue)"/></svg>
    </div>
    <h3 class="service-title">Voice</h3>
    <p class="service-text">Lorem Ipsum is simply dummy text of the printing and typesetting industry. Lorem Ipsum has been the industry's 1500s been the industry's 1500s</p>
    <span class="read-link">READ MORE <svg width="10" height="10" viewBox="0 0 10 10"><circle cx="5" cy="5" r="5" fill="var(--ink)"/><path d="M4 3l2 2-2 2" stroke="#fff" stroke-width="1.3" fill="none"/></svg></span>
  </article>
</section>

<section class="why abs">
  <h2 class="section-title" style="top:55px">Why Vantora IT</h2>
  <p class="why-lead">Neque porro quisquam est qui dolorem ipsum quia dolor sit amet, consectetur</p>
  <p class="why-body">Lorem Ipsum is simply dummy text of the printing and typesetting industry. Lorem Ipsum has been the industry's standard dummy text ever since the 1500s, wheLorem Ipsum is simply dummy text of the printing and typesetting industry. Lorem Ipsum has been the industry's standard dummy text ever since the 1500s, whe orem Ipsum has been the industry's</p>
</section>

<section class="blog abs">
  <h2 class="section-title" style="top:50px">Check Out Our Blog</h2>
  <p class="blog-intro">Lorem ipsum is simply dummy text of the printing and typesetting industry. Lorem Ipsum has been the industry's standard dummy text ever since the 1500s, when an unknown printer took a galley of type and scrambled it to make a type specimen book.Lorem ipsum is simply dummy text</p>
  <article class="post abs" style="left:97px">
    <div class="post-image office" role="img" aria-label="Overhead view of a busy office desk with computers and paperwork"></div>
    <h3 class="post-title">Lorem Ipsum is simply dummy text of the printing and typesetting</h3>
    <p class="post-text">Lorem Ipsum is simply dummy text of the printing and typesetting industry. Lorem Ipsum has been the industry's standard dummy text ever since the 1500s, when an unknown printer took a galley of type and scrambled it to make a type specimen book.</p>
    <a class="btn post-btn" href="#">READ MORE</a>
  </article>
  <article class="post abs" style="left:616px">
    <div class="post-image tablet" role="img" aria-label="Hands holding a tablet computer over a desk"></div>
    <h3 class="post-title">Lorem Ipsum is simply dummy text of the printing and typesetting</h3>
    <p class="post-text">Lorem Ipsum is simply dummy text of the printing and typesetting industry. Lorem Ipsum has been the industry's standard dummy text ever since the 1500s, when an unknown printer took a galley of type and scrambled it to make a type specimen book.</p>
    <a class="btn post-btn" href="#">READ MORE</a>
  </article>
</section>

<div class="divider abs"></div>

<form class="subscribe abs">
  <div class="subscribe-input">EMAIL ADDRESS</div>
  <div class="subscribe-btn">SUBSCRIBE</div>
</form>

<footer class="site-footer abs">
  <div class="footer-col" style="left:102px">
    <h4>Main Menu</h4>
    <a href="#">Home</a><a href="#">Services</a><a href="#">Blog</a><a href="#">About</a><a href="#">Contact</a>
  </div>
  <div class="footer-col" style="left:360px">
    <h4>Help</h4>
    <a href="#">Faq</a><a href="#">Team</a><a href="#">Serivce</a><a href="#">Privacy Policy</a>
  </div>
  <div class="footer-col account" style="left:613px">
    <h4>Account</h4>
    <a href="#">Login</a><a href="#">Register</a>
  </div>
  <div class="footer-col" style="left:801px">
    <h4>About us</h4>
    <p>Lorem ipsum is simply dummy text of the printing and typesetting industry. Lorem Ipsum has been the industry's standard dummy text ever since the 1500s</p>
  </div>
  <div class="footer-rule abs"></div>
  <div class="social abs"><span></span><span></span><span></span><span></span></div>
  <p class="copyright abs">Vantora © 2017 All Rights Reserved</p>
  <div class="footer-brand abs"><span class="brand-mark"></span><span class="brand-name">Vantora IT</span></div>
  <nav class="footer-links abs"><a href="#">Contact</a><a href="#">FAQ</a><a href="#">Terms Privacy</a><a href="#">Blog</a></nav>
  <p class="footer-phone abs">888-555-0147</p>
  <p class="footer-email abs">support@vantora.example</p>
</footer>

</body>
</html>
```